Road Construction Company needs business cards

We would like a new business card designed for our business.

We're a road construction company based in Qld, Australia.

Can the business card please have the following information on it.

Name: Warren Halbeck
Position: General Manager
Phone: 0472 915 348
Email: Warren.halbeck@tovrin.com.au
Address: 87 Marrow Ave, Pendlebay, QLD, 4023
Website: www.tovrin.com.au

Visually we'd like the card to be professional and simple.

Attached is our logo.

Our website is www.tovrin.com.au

Target Market(s)

Men aged 25-60

Contact Information for Business Card

As listed in project description

Font styles to use
Serif

Requirements
Must have
• Large logo on back of card

```html
<!DOCTYPE html>
<html lang="en">
<head>
<meta charset="utf-8">
<title>Tovrin – Business Card</title>
<link rel="stylesheet" href="https://fonts.googleapis.com/css2?family=Ubuntu:wght@400;500;700&display=swap">
<style>
  :root {
    --backdrop: #e6e6e6;
    --brand-blue: #0a56a2;
    --brand-navy: #0f2f6e;
    --accent-sky: #2fa6db;
    --paper: #ffffff;
    --ink: #4a4a4a;
  }
  html, body {
    margin: 0;
    padding: 0;
    width: 1200px;
    height: 588px;
    overflow: hidden;
    background: var(--backdrop);
    font-family: "Ubuntu", sans-serif;
  }
  .canvas {
    position: relative;
    width: 1200px;
    height: 588px;
  }
  .card {
    position: absolute;
    top: 142px;
    width: 488px;
    height: 287px;
    overflow: hidden;
  }
  .card--back {
    left: 87px;
    background: var(--brand-blue);
    display: flex;
    align-items: center;
    justify-content: center;
  }
  .card--back .wordmark {
    font-size: 60px;
    font-weight: 700;
    letter-spacing: 4px;
    color: var(--brand-navy);
    line-height: 1;
    margin-top: -6px;
  }
  .card--front {
    left: 622px;
    background: var(--paper);
  }
  .card--front .wordmark {
    position: absolute;
    right: 24px;
    top: 24px;
    font-size: 34px;
    font-weight: 700;
    letter-spacing: 2px;
    color: var(--brand-blue);
    line-height: 1;
  }
  .person {
    position: absolute;
    left: 23px;
    top: 131px;
  }
  .person__name {
    margin: 0;
    font-size: 18.5px;
    font-weight: 700;
    color: var(--brand-blue);
    line-height: 1.1;
  }
  .person__role {
    margin: 3px 0 0;
    font-size: 13px;
    color: var(--ink);
  }
  .divider {
    position: absolute;
    left: 23px;
    right: 24px;
    top: 184px;
    height: 1px;
    background: var(--brand-blue);
  }
  .contacts {
    position: absolute;
    left: 23px;
    top: 202px;
    margin: 0;
    padding: 0;
    list-style: none;
    font-size: 13px;
    color: var(--ink);
  }
  .contacts li {
    display: flex;
    align-items: center;
    height: 19px;
  }
  .contacts svg {
    width: 11px;
    height: 11px;
    margin-right: 5px;
    flex: none;
  }
  .address {
    position: absolute;
    right: 24px;
    top: 221px;
    margin: 0;
    font-style: normal;
    font-size: 13px;
    line-height: 19px;
    color: var(--ink);
    text-align: right;
  }
  .band {
    position: absolute;
    left: 0;
    right: 0;
    bottom: 0;
    height: 11px;
    background: var(--brand-blue);
  }
  .band__accent {
    position: absolute;
    left: 344px;
    width: 120px;
    top: 0;
    bottom: 0;
    background: var(--accent-sky);
    border-left: 2px solid var(--paper);
    border-right: 2px solid var(--paper);
  }
</style>
</head>
<body>
<main class="canvas">
  <section class="card card--back" aria-label="Card back">
    <span class="wordmark">TOVRIN</span>
  </section>

  <section class="card card--front" aria-label="Card front">
    <span class="wordmark">TOVRIN</span>

    <div class="person">
      <h1 class="person__name">WARREN HALBECK</h1>
      <p class="person__role">General Manager</p>
    </div>

    <div class="divider"></div>

    <ul class="contacts">
      <li>
        <svg viewBox="0 0 24 24" aria-hidden="true"><path fill="#2fa6db" d="M6.6 10.8a15.1 15.1 0 0 0 6.6 6.6l2.2-2.2a1 1 0 0 1 1-.25 11.4 11.4 0 0 0 3.6.57 1 1 0 0 1 1 1V20a1 1 0 0 1-1 1A17 17 0 0 1 3 4a1 1 0 0 1 1-1h3.5a1 1 0 0 1 1 1c0 1.25.2 2.45.57 3.57a1 1 0 0 1-.25 1z"/></svg>
        0472 915 348
      </li>
      <li>
        <svg viewBox="0 0 24 24" aria-hidden="true"><rect x="2" y="5" width="20" height="14" rx="1" fill="#2fa6db"/><path d="M2 6l10 7 10-7" fill="none" stroke="#fff" stroke-width="1.6"/></svg>
        Warren.halbeck@tovrin.com.au
      </li>
      <li>
        <svg viewBox="0 0 24 24" aria-hidden="true"><circle cx="12" cy="12" r="10" fill="#2fa6db"/><path d="M2 12h20M12 2c3 3 3 17 0 20M12 2c-3 3-3 17 0 20" fill="none" stroke="#fff" stroke-width="1.4"/></svg>
        www.tovrin.com.au
      </li>
    </ul>

    <address class="address">87 Marrow Ave<br>Pendlebay, QLD, 4023</address>

    <div class="band"><span class="band__accent"></span></div>
  </section>
</main>
</body>
</html>
```